Business Card Design Project

Business Card
We are rebranding with a new logo
Industry/Entity Type
Business
Contact Information for Business Card
Dennis Morvale +61 487215963 dennis@quorv.com.au P.O. Box 872 Fernlow QLD 4309
Requirements
Must have
- Logo

```html
<!DOCTYPE html>
<html lang="en">
<head>
<meta charset="utf-8">
<title>Business Card – Dennis Morvale</title>
<link rel="stylesheet" href="https://fonts.googleapis.com/css2?family=Roboto:wght@400;500;700&display=swap">
<style>
  :root {
    --stage: #2b2b2b;
    --card-white: #f3f3f3;
    --blue-deep: #064563;
    --blue-glow: #1392c2;
    --orange: #ef8a1f;
    --text-light: #ffffff;
    --icon-line: #0b5c80;
    --brand-blue: #0b6b98;
  }
  html, body {
    margin: 0;
    width: 1200px;
    height: 960px;
    overflow: hidden;
    background: var(--stage);
  }
  .card {
    position: absolute;
    left: 224px;
    top: 266px;
    width: 753px;
    height: 429px;
    border-radius: 20px;
    overflow: hidden;
    background: var(--card-white);
    font-family: "Roboto", Arial, sans-serif;
  }
  .side-panel {
    position: absolute;
    inset: 0;
    clip-path: polygon(0 0, 440px 0, 226px 429px, 0 429px);
    background: radial-gradient(circle at 120px 240px, var(--blue-glow) 0%, var(--blue-deep) 85%);
  }
  .contact {
    position: absolute;
    left: 54px;
    top: 72px;
    color: var(--text-light);
  }
  .contact-name {
    margin: 0 0 16px;
    font-size: 24px;
    font-weight: 500;
    color: var(--orange);
    letter-spacing: 0.2px;
  }
  .contact-address {
    margin: 0 0 10px;
    font-size: 18px;
    line-height: 23px;
    font-style: normal;
  }
  .contact-list {
    list-style: none;
    margin: 0;
    padding: 0;
    font-size: 18px;
    line-height: 24px;
  }
  .contact-list li {
    display: flex;
    align-items: center;
    gap: 9px;
  }
  .contact-icon {
    width: 17px;
    height: 17px;
    flex: none;
    fill: var(--orange);
  }
  .brand {
    position: absolute;
    left: 440px;
    top: 300px;
    width: 260px;
    margin: 0;
    text-align: center;
    font-size: 30px;
    font-weight: 500;
    line-height: 40px;
    color: var(--brand-blue);
    letter-spacing: 1px;
  }
</style>
</head>
<body>
  <section class="card">
    <div class="side-panel" role="img" aria-label="Blue gradient side panel with orange decorative swoosh"></div>

    <div class="contact">
      <h1 class="contact-name">DENNIS MORVALE</h1>
      <address class="contact-address">P.O. Box 872<br>Fernlow QLD 4309</address>
      <ul class="contact-list">
        <li>
          <svg class="contact-icon" viewBox="0 0 24 24" aria-hidden="true"><path d="M6.6 10.8a15 15 0 0 0 6.6 6.6l2.2-2.2c.3-.3.7-.4 1-.2 1.1.4 2.3.6 3.6.6.6 0 1 .4 1 1V20c0 .6-.4 1-1 1A17 17 0 0 1 3 4c0-.6.4-1 1-1h3.5c.6 0 1 .4 1 1 0 1.3.2 2.5.6 3.6.1.3 0 .7-.2 1z"/></svg>
          +61 487215963
        </li>
        <li>
          <svg class="contact-icon" viewBox="0 0 24 24" aria-hidden="true"><path d="M2 5h20v14H2z"/><path d="M3 6.5l9 6.5 9-6.5" fill="none" stroke="var(--icon-line)" stroke-width="1.5"/></svg>
          dennis@quorv.com.au
        </li>
        <li>
          <svg class="contact-icon" viewBox="0 0 24 24" aria-hidden="true"><circle cx="12" cy="12" r="10"/><path d="M2 12h20M12 2c3 3 3 17 0 20M12 2c-3 3-3 17 0 20" fill="none" stroke="var(--icon-line)" stroke-width="1.5"/></svg>
          www.quorv.com.au
        </li>
      </ul>
    </div>

    <p class="brand">QUORV<br>INTERNATIONAL</p>
  </section>
</body>
</html>
```